New Business Card Design Project

Use the flyer uploaded and website www.brightoakbuilders.com for inspiration.
List Our Services on Backside of business cards
Marcus Delling
Harborline Builders Inc.
Licensed General Contractors
858-471-6093

Contact Information for Business Card

Use the flyer uploaded and website www.brightoakbuilders.com for inspiration. List Our Services on Backside of business cards Marcus Delling Harborline Builders Inc. Licensed General Contractors 858-471-6093

```html
<!DOCTYPE html>
<html lang="en">
<head>
<meta charset="utf-8">
<title>Harborline Builders – Business Card</title>
<link rel="stylesheet" href="https://fonts.googleapis.com/css2?family=Cinzel:wght@400&family=Arimo:wght@400&display=swap">
<style>
  :root {
    --page: #e4e4e4;
    --card-light: #efefef;
    --card-dark: #2f2f2f;
    --stripe: #a9a8a9;
    --ink: #2a2a2a;
    --white: #ffffff;
    --art-top: #3a3a3a;
    --art-bottom: #333333;
  }
  * { margin: 0; padding: 0; box-sizing: border-box; }
  html, body { width: 1200px; height: 1040px; overflow: hidden; background: var(--page); }
  .canvas { position: relative; width: 1200px; height: 1040px; }

  .card {
    position: absolute;
    left: 278px;
    width: 644px;
    height: 368px;
    border-radius: 18px;
    overflow: hidden;
    box-shadow: 0 2px 3px rgba(0,0,0,0.35);
  }
  .card--front { top: 128px; background: var(--card-light); }
  .card--back  { top: 568px; background: var(--card-dark); }

  .front-shape { position: absolute; inset: 0; }

  .holder-name {
    position: absolute; left: 28px; top: 90px;
    font-family: "Cinzel", serif; font-size: 26px; color: var(--ink);
    letter-spacing: 0.5px;
  }
  .contact-list {
    position: absolute; left: 28px; top: 149px; list-style: none;
    font-family: "Arimo", sans-serif; font-size: 16.5px; color: var(--ink);
  }
  .contact-list li { display: flex; align-items: center; height: 20px; }
  .contact-list svg { width: 14px; height: 14px; margin-right: 6px; fill: var(--ink); }
  .company-lines {
    position: absolute; left: 28px; top: 230px;
    font-family: "Arimo", sans-serif; font-size: 16.5px; color: var(--ink); line-height: 20px;
  }
  .brand-name {
    position: absolute; left: 370px; width: 244px; top: 196px; text-align: center;
    font-family: "Cinzel", serif; font-size: 19px; color: var(--white); letter-spacing: 1.5px;
  }

  .services-title {
    position: absolute; left: 44px; top: 34px;
    font-family: "Cinzel", serif; font-size: 21px; color: var(--white);
  }
  .services-list {
    position: absolute; left: 44px; top: 68px; list-style: none;
    font-family: "Arimo", sans-serif; font-size: 16.5px; color: var(--white);
  }
  .services-list li { display: flex; align-items: center; height: 23.5px; }
  .services-list li::before {
    content: ""; width: 7px; height: 7px; background: var(--white); margin-right: 12px;
  }
  .back-art {
    position: absolute; left: 296px; top: 108px; width: 348px; height: 260px;
    background: linear-gradient(160deg, var(--art-top), var(--art-bottom));
  }
</style>
</head>
<body>
<main class="canvas">
  <section class="card card--front">
    <svg class="front-shape" viewBox="0 0 644 368" width="644" height="368" aria-hidden="true">
      <polygon points="466,0 644,0 644,368 466,368 282,184" fill="var(--card-dark)"/>
      <polygon points="470,0 478,0 306,184 478,368 470,368 292,184" fill="var(--stripe)"/>
    </svg>
    <h1 class="holder-name">MARCUS DELLING</h1>
    <ul class="contact-list">
      <li><svg viewBox="0 0 24 24"><path d="M6.6 10.8a15 15 0 0 0 6.6 6.6l2.2-2.2a1 1 0 0 1 1-.25 11.4 11.4 0 0 0 3.6.57 1 1 0 0 1 1 1V20a1 1 0 0 1-1 1A17 17 0 0 1 3 4a1 1 0 0 1 1-1h3.5a1 1 0 0 1 1 1c0 1.25.2 2.45.57 3.57a1 1 0 0 1-.25 1z"/></svg>858-471-6093</li>
      <li><svg viewBox="0 0 24 24"><path d="M3 6h18v12H3z M3 6l9 7 9-7" fill="none" stroke="var(--ink)" stroke-width="0"/><path d="M3 7.5l9 6 9-6V18H3z M3 5.5h18L12 11.5z"/></svg>info@brightoakbuilders.com</li>
      <li><svg viewBox="0 0 24 24"><circle cx="12" cy="12" r="10"/><path d="M7 8c2 0 3 1 3 3s-2 2-2 4 1 3 1 4M15 5c-1 2 0 3 2 3s3 2 2 4" stroke="var(--card-light)" stroke-width="1.6" fill="none"/></svg>www.brightoakbuilders.com</li>
    </ul>
    <p class="company-lines">Harborline Builders Inc.<br>Licensed General Contractors</p>
    <p class="brand-name">HARBORLINE BUILDERS</p>
  </section>

  <section class="card card--back">
    <h2 class="services-title">SERVICES</h2>
    <ul class="services-list">
      <li>Remodel : Kitchen &amp; Bath</li>
      <li>Painting : Interior &amp; Exterior</li>
      <li>Flooring : Carpet, Vinyl, Wood</li>
      <li>Window &amp; Door Replacement</li>
      <li>Plumbing : Repairs &amp; Upgrades</li>
      <li>Energy- Efficient Upgrades</li>
      <li>Deck &amp; Pation Construction</li>
      <li>Water &amp; Mold Damage</li>
      <li>Garage Renovation</li>
    </ul>
    <div class="back-art" role="img" aria-label="Large line-art brand decoration area"></div>
  </section>
</main>
</body>
</html>
```